Business Card For Halvenmoor Financial Consulting

Hi, I would like a business card designed. Bold, modern.
Please use the same design as the logo. I have also attached the website design to see the overall theme.
Wordmark Font
Color: Hex: #01AEF7

```html
<!DOCTYPE html>
<html lang="en">
<head>
<meta charset="utf-8">
<title>Halvenmoor Financial Consulting – Business Card</title>
<link rel="stylesheet" href="https://fonts.googleapis.com/css2?family=Montserrat:wght@400;500;600;700;800&display=swap">
<style>
  :root {
    --brand-blue: #01aef7;
    --card-black: #050505;
    --backdrop: #3a3a3a;
    --text-white: #f4f4f4;
    --divider: #2c2c2c;
  }
  * { box-sizing: border-box; margin: 0; padding: 0; }
  html, body {
    width: 1200px; height: 689px; overflow: hidden;
    background: var(--backdrop);
    font-family: "Montserrat", sans-serif;
  }
  .canvas {
    position: relative; width: 1200px; height: 689px;
    display: flex; align-items: center; justify-content: center; gap: 30px;
  }
  .card {
    position: relative; width: 555px; height: 318px;
    background: var(--card-black); border-radius: 18px; overflow: hidden;
  }
  .wordmark {
    display: flex; align-items: center; gap: 8px;
    color: var(--text-white); font-weight: 700;
    letter-spacing: 1px; text-transform: uppercase; white-space: nowrap;
    z-index: 2;
  }
  .wordmark-square {
    width: 18px; height: 18px; background: var(--brand-blue); flex: none;
  }
  /* front */
  .card-front .wordmark { position: absolute; left: 30px; top: 44px; font-size: 14px; }
  .tagline {
    position: absolute; left: 30px; bottom: 56px; z-index: 2;
    color: var(--text-white); font-weight: 700; font-size: 18px;
    line-height: 1.22; text-transform: uppercase; letter-spacing: 0.4px;
    white-space: nowrap;
  }
  .tagline .accent { color: var(--brand-blue); }
  .chart-art {
    position: absolute; right: 0; top: 0; width: 245px; height: 318px; z-index: 1;
    background:
      radial-gradient(ellipse at 55% 60%, rgba(1,174,247,0.45), rgba(1,174,247,0.08) 45%, transparent 70%),
      linear-gradient(160deg, #050505 0%, #04202e 55%, #050505 100%);
  }
  /* back */
  .card-back .wordmark { position: absolute; left: 26px; top: 150px; font-size: 13.5px; }
  .back-divider {
    position: absolute; left: 302px; top: 30px; width: 1px; height: 258px;
    background: var(--divider);
  }
  .contact {
    position: absolute; left: 324px; top: 52px; color: var(--text-white);
  }
  .contact-name { font-weight: 700; font-size: 19px; text-transform: uppercase; letter-spacing: 0.5px; white-space: nowrap; }
  .contact-role { color: var(--brand-blue); font-size: 11px; font-weight: 500; text-transform: uppercase; letter-spacing: 1px; margin-top: 3px; }
  .contact-list { list-style: none; margin-top: 18px; font-size: 12.5px; font-weight: 500; }
  .contact-list li { display: flex; align-items: center; gap: 9px; margin-bottom: 6px; white-space: nowrap; }
  .contact-list svg { width: 13px; height: 13px; flex: none; }
  .contact-address { margin-top: 16px; font-size: 12.5px; font-weight: 500; line-height: 1.4; white-space: nowrap; }
</style>
</head>
<body>
<main class="canvas">
  <section class="card card-front">
    <div class="wordmark"><span class="wordmark-square"></span>Halvenmoor Consulting</div>
    <p class="tagline">Helping <span class="accent">your<br>finance team</span> and<br>increasing profit.</p>
    <div class="chart-art" role="img" aria-label="Glowing blue 3D bar chart rising over a lit blue line"></div>
  </section>

  <section class="card card-back">
    <div class="wordmark"><span class="wordmark-square"></span>Halvenmoor Consulting</div>
    <div class="back-divider"></div>
    <div class="contact">
      <p class="contact-name">Marcus Ellery</p>
      <p class="contact-role">Managing Director</p>
      <ul class="contact-list">
        <li>
          <svg viewBox="0 0 24 24"><path fill="#01aef7" d="M6.6 10.8a15 15 0 0 0 6.6 6.6l2.2-2.2c.3-.3.7-.4 1-.2 1.1.4 2.3.6 3.6.6.6 0 1 .4 1 1V20c0 .6-.4 1-1 1A17 17 0 0 1 3 4c0-.6.4-1 1-1h3.5c.6 0 1 .4 1 1 0 1.3.2 2.5.6 3.6.1.3 0 .7-.2 1z"/></svg>
          031-480 275 613
        </li>
        <li>
          <svg viewBox="0 0 24 24"><path fill="#01aef7" d="M2 5h20v14H2z"/><path fill="none" stroke="#050505" stroke-width="1.8" d="M2 5l10 8 10-8"/></svg>
          hello@halvenmoor.com
        </li>
        <li>
          <svg viewBox="0 0 24 24" fill="none" stroke="#01aef7" stroke-width="2"><circle cx="12" cy="12" r="9"/><path d="M3 12h18M12 3c3 3 3 15 0 18M12 3c-3 3-3 15 0 18"/></svg>
          www.halvenmoor.com
        </li>
      </ul>
      <p class="contact-address">17 Larkfield Row, Suite 4<br>30918, Eastmere</p>
    </div>
  </section>
</main>
</body>
</html>
```